Roofing Contractor business card redesign

I want to redesign my business card with a fresh, eye catching concept

Target Market(s)

Residential Roofing Clients, potential employees, and subcontractors.

Industry/Entity Type

Business

Colors

Designer to choose colors to be used in the design.

Requirements
Nice to have
• I just want something that's more pleasing to the eye. You can use a combination of either / or of my logos.

```html
<!DOCTYPE html>
<html lang="en">
<head>
<meta charset="utf-8">
<title>Fair Deal General Contractors – Business Card</title>
<link rel="stylesheet" href="https://fonts.googleapis.com/css2?family=Open+Sans:wght@400;700&family=Oswald:wght@500&display=swap">
<style>
  :root {
    --backdrop: #ece9e4;
    --card-yellow: #fec70a;
    --card-white: #ffffff;
    --brand-brown: #4a1414;
    --accent-orange: #e8731e;
    --ink-grey: #3b3b3b;
  }
  * { box-sizing: border-box; margin: 0; padding: 0; }
  html, body { width: 1200px; height: 900px; overflow: hidden; }
  body { background: var(--backdrop); position: relative; font-family: "Open Sans", Arial, sans-serif; }

  .card {
    position: absolute;
    width: 560px;
    height: 320px;
    box-shadow: 0 6px 18px rgba(0,0,0,.18);
  }
  .card--front { left: 70px; top: 110px; background: var(--card-yellow); display: flex; align-items: center; justify-content: center; }
  .card--back { left: 570px; top: 470px; background: var(--card-white); }

  .brand { display: flex; align-items: center; gap: 12px; color: var(--brand-brown); font-weight: 700; }
  .brand__dot { width: 40px; height: 40px; border-radius: 50%; background: var(--brand-brown); flex: none; }
  .brand__text { line-height: 1.05; }
  .brand__name { font-size: 40px; letter-spacing: -1px; }
  .brand__sub { font-size: 19px; }

  .card--back .brand { position: absolute; right: 34px; top: 30px; }
  .card--back .brand__dot { width: 34px; height: 34px; }
  .card--back .brand__name { font-size: 34px; }
  .card--back .brand__sub { font-size: 16px; }

  .divider { position: absolute; left: 150px; right: 34px; top: 128px; height: 1px; background: var(--brand-brown); }

  .person { position: absolute; left: 34px; top: 168px; }
  .person__name { font-family: "Oswald", Arial, sans-serif; font-weight: 500; font-size: 24px; color: var(--brand-brown); display: flex; align-items: center; gap: 10px; }
  .person__name::after { content: ""; display: block; width: 150px; height: 1px; background: var(--brand-brown); }
  .person__role { color: var(--accent-orange); font-size: 14px; line-height: 1.35; }

  .address { position: absolute; left: 34px; bottom: 30px; color: var(--ink-grey); font-size: 15px; line-height: 1.4; }

  .contacts { position: absolute; right: 34px; top: 150px; list-style: none; color: var(--ink-grey); font-size: 12.5px; line-height: 1.7; text-align: right; }
  .contacts li { display: flex; justify-content: flex-end; align-items: center; gap: 6px; }
  .contacts svg { width: 11px; height: 11px; fill: var(--brand-brown); }
</style>
</head>
<body>
  <section class="card card--front" aria-label="Card front">
    <div class="brand">
      <span class="brand__dot"></span>
      <div class="brand__text">
        <div class="brand__name">Fair Deal</div>
        <div class="brand__sub">General Contractors, Inc.</div>
      </div>
    </div>
  </section>

  <section class="card card--back" aria-label="Card back">
    <div class="brand">
      <span class="brand__dot"></span>
      <div class="brand__text">
        <div class="brand__name">Fair Deal</div>
        <div class="brand__sub">General Contractors, Inc.</div>
      </div>
    </div>
    <div class="divider"></div>

    <div class="person">
      <div class="person__name">Sam Whitlock</div>
      <div class="person__role">Ridgecheck certified Roof Inspector<br>Licensed Property Adjuster</div>
    </div>

    <address class="address" style="font-style:normal">4518 Elm Hollow Drive Suite 110<br>Cedar Falls, TX 75390</address>

    <ul class="contacts">
      <li>(555) 210-4800 <svg viewBox="0 0 12 12"><path d="M1 4c0-2 2-3 5-3s5 1 5 3l-2 1-1-1H4L3 5zM2 6h8v5H2z"/></svg></li>
      <li>(555) 317-2269 <svg viewBox="0 0 12 12"><path d="M3 0h6v12H3zM4 1.5v8h4v-8z"/></svg></li>
      <li>sam@fairdealtx.com <svg viewBox="0 0 12 12"><path d="M0 2h12v8H0zM1 3l5 4 5-4z"/></svg></li>
      <li>www.FairDealGC.com <svg viewBox="0 0 12 12"><circle cx="6" cy="6" r="6"/></svg></li>
    </ul>
  </section>
</body>
</html>
```